A resume/portfolio website for myself

I'm an independent software contractor, architect, tech trainer. I need a web site to present myself. Many ready to use portfolio designs are too artistic and focused on presenting design skills of the person. I like a nice website but the content should be a little less graphic than if you would present a graphic designer. Content could be presentation of me, core skill qualities and services and resume. Potentially a page with my tech courses in the longer run

```html
<!DOCTYPE html>
<html lang="en">
<head>
<meta charset="utf-8">
<title>Jonas Vester – Frontend Specialist / Web Developer</title>
<link href="https://fonts.googleapis.com/css2?family=Montserrat:wght@400;500;600;700&display=swap" rel="stylesheet">
<style>
:root{
  --header:#3b3b3b;
  --header-dark:#2e2e2e;
  --nav:#8a8a8a;
  --page:#f1f1f1;
  --card:#ffffff;
  --border:#e2e2e2;
  --ink:#2b2b2b;
  --muted:#7a7a7a;
  --accent:#1f6fd6;
  --ring:#e4ebf5;
}
*{box-sizing:border-box;margin:0;padding:0}
html,body{width:1200px;height:4180px;overflow:hidden}
body{background:var(--page);font-family:'Montserrat',sans-serif;color:var(--ink);position:relative}

/* Header */
.hero{position:absolute;left:0;top:0;width:1200px;height:736px;background:linear-gradient(180deg,var(--header) 0%,var(--header-dark) 100%);color:#fff;text-align:center}
.brand{position:absolute;left:112px;top:38px;font-size:34px;font-weight:600;letter-spacing:1px}
.download{position:absolute;right:112px;top:30px;height:56px;padding:0 36px;border-radius:28px;background:#4a4a4a;color:#eee;font-size:18px;font-weight:600;letter-spacing:1.5px;display:flex;align-items:center;gap:14px}
.portrait{position:absolute;left:484px;top:146px;width:236px;height:236px;border-radius:46% 54% 50% 50%;background:linear-gradient(160deg,#c9ccd0,#8d939a);box-shadow:-8px 6px 0 #2bb3c0}
.hero-name{position:absolute;left:0;right:0;top:400px;font-size:46px;font-weight:500}
.hero-title{position:absolute;left:0;right:0;top:462px;font-size:24px;font-weight:600}
.hero-intro{position:absolute;left:200px;width:800px;top:512px;font-size:14px;line-height:20px;color:#bdbdbd}
.hero-intro p{margin-bottom:12px}
.contact-strip{position:absolute;left:0;right:0;top:682px;display:flex;justify-content:center;gap:60px;font-size:14px;color:#ddd}
.contact-strip span{display:flex;align-items:center;gap:10px}

/* Nav */
.nav{position:absolute;left:0;top:736px;width:1200px;height:84px;background:var(--nav);display:flex;justify-content:center;align-items:center;gap:44px;color:#fff;font-size:18px;font-weight:500}

/* Cards */
.card{position:absolute;left:108px;width:984px;background:var(--card);border:1px solid var(--border);box-shadow:0 2px 8px rgba(0,0,0,.06)}
.card-title{text-align:center;font-size:26px;font-weight:600;margin-top:44px}

/* Experience */
.experience{top:888px;height:992px}
.timeline{position:absolute;left:262px;top:152px;width:3px;height:760px;background:#cfdbea}
.job{position:absolute;left:44px;width:896px;height:130px}
.job-role{position:absolute;left:0;top:0;font-size:24px;font-weight:700}
.job-date{position:absolute;left:0;top:34px;font-size:15px;font-weight:600;color:#555}
.job-dot{position:absolute;left:208px;top:8px;width:24px;height:24px;border-radius:50%;background:#fff;border:4px solid var(--accent)}
.job-company{position:absolute;left:288px;top:0;font-size:17px;font-weight:700}
.job-summary{position:absolute;left:288px;top:40px;font-size:15px;font-weight:500}
.job-tech{position:absolute;left:288px;top:70px;width:460px;font-size:12px;line-height:17px;color:var(--muted)}
.job-place{position:absolute;right:0;top:0;font-size:15px;color:#555;display:flex;align-items:center;gap:8px}

/* Education */
.education{top:1912px;height:248px}
.school{position:absolute;top:110px}
.school-field{font-size:24px;font-weight:600;color:var(--accent)}
.school-name{font-size:16px;margin-top:12px;color:#444}
.school-years{font-size:16px;margin-top:16px;color:#444}

/* Skills */
.skills{top:2200px;height:760px}
.sub-title{text-align:center;font-size:20px;font-weight:500;margin-top:24px}
.skill{position:absolute;top:150px;width:276px;text-align:center}
.skill svg{display:block;margin:0 auto}
.skill-name{font-size:24px;font-weight:500;margin-top:26px;white-space:nowrap}
.skill-level{font-size:17px;margin-top:8px}
.skill-text{font-size:12px;line-height:17px;color:var(--muted);margin-top:16px;padding:0 20px}
.other-title{position:absolute;left:0;right:0;top:466px;margin-top:0}
.tags{position:absolute;left:92px;width:800px;top:530px;display:flex;flex-wrap:wrap;justify-content:center;gap:22px 26px}
.tag{height:54px;padding:0 30px;border:2px solid #cfcfcf;border-radius:10px;font-size:19px;font-weight:600;display:flex;align-items:center}

/* Portfolio */
.portfolio{top:3000px;height:440px}
.gallery{position:absolute;left:24px;top:116px;display:flex;gap:12px}
.shot{width:224px;height:224px}
.carousel{position:absolute;left:0;right:0;top:378px;display:flex;justify-content:center;gap:40px}

/* Contact */
.contact{top:3480px;height:620px}
.contact-photo{position:absolute;left:72px;top:140px;width:170px;height:170px;border-radius:50%;background:linear-gradient(160deg,#c7cacd,#878d93)}
.contact-body{position:absolute;left:288px;top:140px;width:640px}
.contact-lead{font-size:16px;font-weight:600;line-height:25px}
.offer-title{font-size:16px;font-weight:600;margin-top:30px}
.offer-list{list-style:none;margin-top:14px}
.offer-list li{display:flex;align-items:center;gap:16px;font-size:14px;color:#444;height:34px}
.drop-line{font-size:14px;margin-top:22px;color:#444}
.social{display:flex;gap:26px;margin-top:22px}
.social span{width:14px;height:14px;border-radius:50%;background:#555}

/* Footer */
.footer{position:absolute;left:0;right:0;top:4140px;text-align:center;font-size:15px;color:#333}
</style>
</head>
<body>

<header class="hero">
  <div class="brand">JONAS VESTER</div>
  <div class="download">
    <svg width="20" height="20" viewBox="0 0 20 20"><path d="M10 2v11M5 9l5 5 5-5M3 17h14" fill="none" stroke="#eee" stroke-width="2"/></svg>
    DOWNLOAD MY RESUME
  </div>
  <div class="portrait" role="img" aria-label="Portrait photo of Jonas Vester"></div>
  <h1 class="hero-name">Jonas Vester</h1>
  <div class="hero-title">Frontend Specialist / Web Developer</div>
  <div class="hero-intro">
    <p>I build dependable web applications for teams that value clear code, steady delivery and interfaces people enjoy using every single day, from first sketch to final release.</p>
    <p>Architecture, hands-on development and training are the three pillars of my work.</p>
    <p>I join projects as a contractor, shape the technical direction and help developers grow through practical courses, reviews and pairing sessions that last.</p>
    <p>Working with clients across many countries on both long and short engagements.</p>
  </div>
  <div class="contact-strip">
    <span><svg width="18" height="14" viewBox="0 0 18 14"><rect x="1" y="1" width="16" height="12" fill="none" stroke="#ddd" stroke-width="1.6"/><path d="M1 1l8 7 8-7" fill="none" stroke="#ddd" stroke-width="1.6"/></svg>jonas.vester@example.com</span>
    <span><svg width="16" height="16" viewBox="0 0 16 16"><path d="M3 1h3l1.5 4-2 1.2a9 9 0 0 0 4.3 4.3L11 8.5l4 1.5v3a2 2 0 0 1-2 2A12 12 0 0 1 1 3a2 2 0 0 1 2-2z" fill="#ddd"/></svg>+1 555 014 2290</span>
  </div>
</header>

<nav class="nav">
  <span>Experience</span><span>Education</span><span>Skills</span><span>Accomplishments</span><span>Portfolio</span><span>Contact</span>
</nav>

<section class="card experience">
  <h2 class="card-title">Work Experiences</h2>
  <div class="timeline"></div>

  <div class="job" style="top:168px">
    <div class="job-role">Job Position</div><div class="job-date">Apr 2020 – Present</div>
    <div class="job-dot"></div>
    <div class="job-company">Tavlo Assist</div>
    <div class="job-summary">Development of a brand new customer oriented application.</div>
    <div class="job-tech">Tools: component frameworks, typed scripting, responsive layout, design systems, REST services, version control, automated testing, continuous delivery, agile teamwork, code review.</div>
    <div class="job-place"><svg width="12" height="16" viewBox="0 0 12 16"><path d="M6 0a6 6 0 0 1 6 6c0 4-6 10-6 10S0 10 0 6a6 6 0 0 1 6-6z" fill="#888"/><circle cx="6" cy="6" r="2" fill="#fff"/></svg>Harborview</div>
  </div>

  <div class="job" style="top:328px">
    <div class="job-role">Job Position</div><div class="job-date">Apr 2020 – Present</div>
    <div class="job-dot"></div>
    <div class="job-company">Qerion Systems</div>
    <div class="job-summary">Development of a brand new customer oriented application.</div>
    <div class="job-tech">Tools: component frameworks, typed scripting, responsive layout, design systems, REST services, version control, automated testing, continuous delivery, agile teamwork, code review.</div>
    <div class="job-place"><svg width="12" height="16" viewBox="0 0 12 16"><path d="M6 0a6 6 0 0 1 6 6c0 4-6 10-6 10S0 10 0 6a6 6 0 0 1 6-6z" fill="#888"/><circle cx="6" cy="6" r="2" fill="#fff"/></svg>Harborview</div>
  </div>

  <div class="job" style="top:488px">
    <div class="job-role">Job Position</div><div class="job-date">Apr 2020 – Present</div>
    <div class="job-dot"></div>
    <div class="job-company">Brevado</div>
    <div class="job-summary">Development of a brand new customer oriented application.</div>
    <div class="job-tech">Tools: component frameworks, typed scripting, responsive layout, design systems, REST services, version control, automated testing, continuous delivery, agile teamwork, code review.</div>
    <div class="job-place"><svg width="12" height="16" viewBox="0 0 12 16"><path d="M6 0a6 6 0 0 1 6 6c0 4-6 10-6 10S0 10 0 6a6 6 0 0 1 6-6z" fill="#888"/><circle cx="6" cy="6" r="2" fill="#fff"/></svg>Harborview</div>
  </div>

  <div class="job" style="top:648px">
    <div class="job-role">Job Position</div><div class="job-date">Apr 2020 – Present</div>
    <div class="job-dot"></div>
    <div class="job-company">Lunmark Tech</div>
    <div class="job-summary">Development of a brand new customer oriented application.</div>
    <div class="job-tech">Tools: component frameworks, typed scripting, responsive layout, design systems, REST services, version control, automated testing, continuous delivery, agile teamwork, code review.</div>
    <div class="job-place"><svg width="12" height="16" viewBox="0 0 12 16"><path d="M6 0a6 6 0 0 1 6 6c0 4-6 10-6 10S0 10 0 6a6 6 0 0 1 6-6z" fill="#888"/><circle cx="6" cy="6" r="2" fill="#fff"/></svg>Harborview</div>
  </div>

  <div class="job" style="top:808px">
    <div class="job-role">Job Position</div><div class="job-date">Apr 2020 – Present</div>
    <div class="job-dot"></div>
    <div class="job-company">Orvane Business</div>
    <div class="job-summary">Development of a brand new customer oriented application.</div>
    <div class="job-tech">Tools: component frameworks, typed scripting, responsive layout, design systems, REST services, version control, automated testing, continuous delivery, agile teamwork, code review.</div>
    <div class="job-place"><svg width="12" height="16" viewBox="0 0 12 16"><path d="M6 0a6 6 0 0 1 6 6c0 4-6 10-6 10S0 10 0 6a6 6 0 0 1 6-6z" fill="#888"/><circle cx="6" cy="6" r="2" fill="#fff"/></svg>Harborview</div>
  </div>
</section>

<section class="card education">
  <h2 class="card-title">Education</h2>
  <div class="school" style="left:168px">
    <div class="school-field">Information Technology</div>
    <div class="school-name">Norrvik University</div>
    <div class="school-years">2002 – 2005</div>
  </div>
  <div class="school" style="left:592px">
    <div class="school-field">Computer Science</div>
    <div class="school-name">Business College</div>
    <div class="school-years">1996 – 2000</div>
  </div>
</section>

<section class="card skills">
  <h2 class="card-title">Professional Skills</h2>
  <div class="sub-title">Top Skills</div>

  <div class="skill" style="left:74px">
    <svg width="160" height="160" viewBox="0 0 160 160">
      <circle cx="80" cy="80" r="66" fill="none" stroke="var(--ring)" stroke-width="16"/>
      <circle cx="80" cy="80" r="66" fill="none" stroke="var(--accent)" stroke-width="16" stroke-dasharray="406.4 414.7" transform="rotate(-90 80 80)"/>
      <text x="80" y="92" text-anchor="middle" font-family="Montserrat, sans-serif" font-size="34" font-weight="500" fill="#2b2b2b">98%</text>
    </svg>
    <div class="skill-name">Scripting</div>
    <div class="skill-level">Expert</div>
    <div class="skill-text">Years of practical work on large single page applications, from architecture to testing and tuning.</div>
  </div>

  <div class="skill" style="left:350px">
    <svg width="160" height="160" viewBox="0 0 160 160">
      <circle cx="80" cy="80" r="66" fill="none" stroke="var(--ring)" stroke-width="16"/>
      <circle cx="80" cy="80" r="66" fill="none" stroke="var(--accent)" stroke-width="16" stroke-dasharray="410.6 414.7" transform="rotate(-90 80 80)"/>
      <text x="80" y="92" text-anchor="middle" font-family="Montserrat, sans-serif" font-size="34" font-weight="500" fill="#2b2b2b">99%</text>
    </svg>
    <div class="skill-name">Web UI, 4 years</div>
    <div class="skill-level">Expert</div>
    <div class="skill-text">Years of practical work on large single page applications, from architecture to testing and tuning.</div>
  </div>

  <div class="skill" style="left:642px">
    <svg width="160" height="160" viewBox="0 0 160 160">
      <circle cx="80" cy="80" r="66" fill="none" stroke="var(--ring)" stroke-width="16"/>
      <circle cx="80" cy="80" r="66" fill="none" stroke="var(--accent)" stroke-width="16" stroke-dasharray="373.2 414.7" transform="rotate(-90 80 80)"/>
      <text x="80" y="92" text-anchor="middle" font-family="Montserrat, sans-serif" font-size="34" font-weight="500" fill="#2b2b2b">90%</text>
    </svg>
    <div class="skill-name">Typing, 4 years</div>
    <div class="skill-level">Advanced</div>
    <div class="skill-text">Years of practical work on large single page applications, from architecture to testing and tuning.</div>
  </div>

  <div class="sub-title other-title">Other Skills</div>
  <div class="tags">
    <span class="tag">Markup</span><span class="tag">Styling</span><span class="tag">Design Systems</span><span class="tag">UI Grids</span>
    <span class="tag">Preprocessing</span><span class="tag">Version Control</span><span class="tag">Cloud</span><span class="tag">Backend</span>
  </div>
</section>

<section class="card portfolio">
  <h2 class="card-title">Portfolio</h2>
  <div class="gallery">
    <div class="shot" role="img" aria-label="Project screenshot shown on laptop and tablet" style="background:linear-gradient(150deg,#3d5f8a,#9fb6cc)"></div>
    <div class="shot" role="img" aria-label="Illustrated web application project preview" style="background:linear-gradient(150deg,#2f86b8,#e07f8c)"></div>
    <div class="shot" role="img" aria-label="Website layout mockups with red accents" style="background:linear-gradient(150deg,#c9c9c9,#e6a3a3)"></div>
    <div class="shot" role="img" aria-label="Dark website homepage project preview" style="background:linear-gradient(150deg,#4a3a2a,#d9c7a8)"></div>
  </div>
  <div class="carousel">
    <svg width="14" height="20" viewBox="0 0 14 20"><path d="M10 3L3 10l7 7" fill="none" stroke="#222" stroke-width="3"/></svg>
    <svg width="14" height="20" viewBox="0 0 14 20"><path d="M4 3l7 7-7 7" fill="none" stroke="#222" stroke-width="3"/></svg>
  </div>
</section>

<section class="card contact">
  <h2 class="card-title">Get in Touch</h2>
  <div class="contact-photo" role="img" aria-label="Round portrait photo of Jonas Vester"></div>
  <div class="contact-body">
    <p class="contact-lead">I help teams plan, build and ship modern web applications. Whether you need an architect, an extra developer or a trainer, feel free to get in touch and tell me about your project.</p>
    <div class="offer-title">I can help with the following:</div>
    <ul class="offer-list">
      <li><svg width="16" height="12" viewBox="0 0 16 12"><path d="M1 6l5 5L15 1" fill="none" stroke="#333" stroke-width="2.2"/></svg>Frontend architecture and reviews</li>
      <li><svg width="16" height="12" viewBox="0 0 16 12"><path d="M1 6l5 5L15 1" fill="none" stroke="#333" stroke-width="2.2"/></svg>Web application development</li>
      <li><svg width="16" height="12" viewBox="0 0 16 12"><path d="M1 6l5 5L15 1" fill="none" stroke="#333" stroke-width="2.2"/></svg>Team training and workshops</li>
      <li><svg width="16" height="12" viewBox="0 0 16 12"><path d="M1 6l5 5L15 1" fill="none" stroke="#333" stroke-width="2.2"/></svg>Performance and accessibility audits</li>
      <li><svg width="16" height="12" viewBox="0 0 16 12"><path d="M1 6l5 5L15 1" fill="none" stroke="#333" stroke-width="2.2"/></svg>Shared design systems</li>
      <li><svg width="16" height="12" viewBox="0 0 16 12"><path d="M1 6l5 5L15 1" fill="none" stroke="#333" stroke-width="2.2"/></svg>Long term contract work</li>
    </ul>
    <p class="drop-line">Drop me a line at jonas.vester@example.com or call me at +1 555 014 2290</p>
    <div class="social" aria-label="Social profiles"><span></span><span></span><span></span><span></span></div>
  </div>
</section>

<footer class="footer">© 2020 | www.vesterdev.com</footer>

</body>
</html>
```